Brightmoor - a website to encourage people to spend time in nature

I have a squarespace site with some content on it but the squarespace template doesn't completely suit my needs, I keep fiddling with the template but actually I need some professional help to get it looking the way I want and with the right 'mood'.
The website is for "Brightmoor" - it will be a blog where I write about the importance of nature for good health. I also want to use the website to market services such as outdoor coaching, retreats and walking workshops.
This has been in my head for a LONG time and I currently only use instagram for micro-blogs but it's time for me to get this moving. I've previously engaged other designers on branding for it but they just didn't get it quite the way that I wanted it and I wasn't completely happy with the results. It's been a process for me as to what I want but in the meantime I just didn't come back to the design aspect of it now. I'm looking for a designer who understands the purpose of the website, the ethos and can help me realise this into a design that's clean, clear and simple.

Please note that I have a domain (brightmoor.org) and a lot of content drafted on squarespace already. I have published it with password protection - password is brightmoor2020 - it still has some of the original template on it, but does have some content. Don't take it as anything to follow in particular, i am looking for fresh eyes and fresh ideas.

Target Market(s)

There are three main groups that I want to target - people who are suffering from stress and anxiety, people who treat them and parents who want to get their kids outside (thereby preventing stress and anxiety)

Contact Information for Business Card

Joan Petrie
Brightmoor
Telephone +44 7700 900417
brightmoor@mailvane.com

Logo Text

Brightmoor - if that. I have an idea that the logo should have a leaf on it somewhere, or maybe just be a leaf.

Coding

Coded - Design and coding required

Number of Pages Required

5+ page

Font styles to use
Serif
Sans Serif

Colors
add136
33b8a4
34a6d7
3377b5

Requirements
Must have
• Space for lots of images. The ability for me to edit the pages if I need to. Be user friendly. Look beautiful.
• For an idea of the images I use and the content I'm interested in writing about have a look at @brightmoor on instagram.
• That pop up about cookies so I am complying with data laws.
Should not have
• Must not be too 'busy' I'd like to avoid too much movement.

```html
<!DOCTYPE html>
<html lang="en">
<head>
<meta charset="utf-8">
<title>Brightmoor</title>
<link href="https://fonts.googleapis.com/css2?family=Montserrat:wght@400;500;600;700;800&family=Pinyon+Script&display=swap" rel="stylesheet">
<style>
:root{
  --ink:#111314;
  --white:#ffffff;
  --line:#e2e4e6;
  --mist:#eef1f3;
  --panel:#f3f5f6;
  --dark:#1d1f21;
  --darker:#151718;
  --accent:#d0312d;
  --muted:#b5b8ba;
  --text:#2a2c2e;
}
*{box-sizing:border-box;margin:0;padding:0}
html,body{width:1200px;height:3221px;overflow:hidden;background:var(--white)}
body{position:relative;font-family:"Montserrat",Arial,sans-serif;color:var(--ink)}
.abs{position:absolute}

/* header */
.site-header{left:0;top:0;width:1200px;height:123px;border:1px solid var(--line);background:var(--white)}
.btn-subscribe{left:34px;top:61px;width:108px;height:33px;background:var(--ink);color:var(--white);font-size:9px;font-weight:700;letter-spacing:.3px;display:flex;align-items:center;justify-content:center}
.brand{left:0;width:1200px;top:24px;text-align:center;font-family:"Pinyon Script",cursive;font-size:52px;color:var(--ink)}
.header-icons{top:60px;left:1020px;width:160px;height:20px}

/* hero */
.hero-photo{left:34px;top:125px;width:536px;height:515px;background:linear-gradient(160deg,#c9ccc7 0%,#6d7c5c 45%,#3e5a28 75%,#7a9b45 100%)}
.hero-frame{left:478px;top:239px}
.hero-title{left:594px;top:318px;font-family:"Pinyon Script",cursive;font-size:60px;line-height:1;color:var(--ink);white-space:nowrap}
.hero-sub{left:594px;top:383px;font-size:16.5px;color:var(--ink)}

/* about */
.about-band{left:0;top:621px;width:1200px;height:572px;background:linear-gradient(180deg,#f4f6f7 0%,#e7ebee 55%,#f1f3f4 100%)}
.about-photo{left:446px;top:726px;width:535px;height:423px;background:linear-gradient(180deg,#c7ccd1 0%,#aeb5b8 50%,#5a6560 75%,#e6e8ea 100%)}
.about-heading{left:208px;top:774px;font-size:57px;font-weight:700;letter-spacing:-.5px}
.about-card{left:209px;top:855px;width:405px;height:256px;background:var(--white);padding:40px 34px 0}
.about-card .rule{width:50px;height:3px;background:var(--ink)}
.about-card h2{margin-top:18px;font-size:16.5px;font-weight:600;line-height:1.3}
.about-card p{margin-top:28px;font-size:9.2px;line-height:1.36;text-align:justify;color:var(--text)}

/* blog */
.blog-head{left:208px;top:1240px;font-size:17px;font-weight:600}
.blog-head .rule{width:52px;height:3px;background:var(--ink);margin-top:12px}
.blog-grid{left:208px;top:1320px;width:784px;display:grid;grid-template-columns:repeat(3,250px);grid-template-rows:repeat(3,411px);column-gap:17px;row-gap:0}
.post .thumb{width:250px;height:244px}
.post h3{margin-top:12px;font-size:16.5px;font-weight:700;white-space:nowrap}
.post .meta{margin-top:3px;font-size:8.5px;padding-left:3px}
.post .meta .tag{color:var(--accent);font-weight:600}
.post .meta .date{color:var(--muted);margin-left:10px}
.post p{margin-top:12px;font-size:8.6px;line-height:1.45;text-align:justify;color:var(--text);padding:0 3px}
.pager{top:2525px;width:32px;height:32px;border:1px solid var(--line);border-radius:50%}
.view-all{left:936px;top:2535px;font-size:9px;font-weight:700}
.view-all span{margin-left:12px}

/* subscribe */
.sub-frame{left:566px;top:2634px;width:236px;height:220px;border:8px solid #ececec}
.sub-light{left:221px;top:2669px;width:350px;height:150px;background:var(--panel);display:flex;align-items:center;padding-left:62px;font-size:31px;font-weight:800}
.sub-dark{left:595px;top:2669px;width:375px;height:150px;background:var(--dark)}
.sub-dark .label{position:absolute;left:72px;top:70px;font-size:8.5px;color:var(--white)}
.sub-dark .field{position:absolute;left:72px;top:89px;width:188px;height:1px;background:#4a4d50}
.sub-dark .send{position:absolute;left:268px;top:57px;width:43px;height:43px;border-radius:50%;background:var(--white);display:flex;align-items:center;justify-content:center}

/* footer */
.site-footer{left:0;top:2950px;width:1200px;height:221px;background:var(--dark);color:var(--white);text-align:center;font-size:13px;padding-top:62px}
.site-footer li{list-style:none;height:29.3px}
.copyright{left:0;top:3171px;width:1200px;height:50px;background:var(--darker);color:var(--white);font-size:10.5px;display:flex;align-items:center;justify-content:center}
</style>
</head>
<body>

<header class="abs site-header">
  <div class="abs btn-subscribe">SUBSCRIBE</div>
  <div class="abs brand">Brightmoor</div>
  <svg class="abs header-icons" width="160" height="20" viewBox="0 0 160 20" aria-label="Social and menu">
    <circle cx="11" cy="10" r="5" fill="none" stroke="#111314" stroke-width="1.4"/>
    <circle cx="52" cy="10" r="4.5" fill="#111314"/>
    <rect x="85" y="5.5" width="12" height="9" fill="none" stroke="#111314" stroke-width="1.2"/>
    <path d="M85 6l6 5 6-5" fill="none" stroke="#111314" stroke-width="1.2"/>
    <path d="M134 4.5h14M134 10h14M134 15.5h14" stroke="#111314" stroke-width="1.6"/>
  </svg>
</header>

<div class="abs hero-photo" role="img" aria-label="Path through a green forest of tall trees"></div>
<svg class="abs hero-frame" width="200" height="258" viewBox="0 0 200 258" aria-hidden="true">
  <path d="M8 258V0h192v68h-16V16H24v226h160v-54h16v70z" fill="#000"/>
</svg>
<div class="abs hero-title">Welcome to Brightmoor</div>
<div class="abs hero-sub">The practice of spending time in nature to feel better</div>

<section>
  <div class="abs about-band" role="img" aria-label="Faint snowy mountain landscape"></div>
  <div class="abs about-photo" role="img" aria-label="Snow-covered fir trees in winter fog"></div>
  <h1 class="abs about-heading">Brightmoor</h1>
  <div class="abs about-card">
    <div class="rule"></div>
    <h2>The practice of spending time innature to feel better.</h2>
    <p>Welcome to Brightmoor.&nbsp;&nbsp; An investigation of how spending time in nature helps you to feel better - physically, mentally, spiritually.&nbsp;&nbsp; This started as a personal journey to counteract the effect of too many hours in artificially lit offices, too much stress and too little connection to the natural world.&nbsp; It became something of a mission.&nbsp; To help others re-find their connection to the natural world, and in the process, live better and feel better.</p>
  </div>
</section>

<section>
  <div class="abs blog-head">From the blog<div class="rule"></div></div>
  <div class="abs blog-grid">
    <article class="post"><div class="thumb" role="img" aria-label="Lightbox sign resting on cushions" style="background:linear-gradient(180deg,#4a3a3c 0%,#d9d2cc 45%,#5e4a46 100%)"></div><h3>Brightmoor Article&nbsp; 1</h3><div class="meta"><span class="tag">Physically&nbsp; spiritually</span><span class="date">/ Jan 2020</span></div><p>Welcome to Brightmoor.&nbsp;&nbsp; An investigation of how spending time in nature helps you to feel better - physically, mentally, spiritually.</p></article>
    <article class="post"><div class="thumb" role="img" aria-label="Swimmer on an inflatable in green water" style="background:linear-gradient(160deg,#2f8a72,#5fb39a 50%,#2a7a66)"></div><h3>Brightmoor Article&nbsp; 2</h3><div class="meta"><span class="tag">Physically&nbsp; mentally</span><span class="date">/ Jan 2020</span></div><p>Welcome to Brightmoor.&nbsp;&nbsp; An investigation of how spending time in nature helps you to feel better - physically, mentally, spiritually.</p></article>
    <article class="post"><div class="thumb" role="img" aria-label="Woman in a hat among dry grasses" style="background:linear-gradient(180deg,#e4e6e6 0%,#b9a283 50%,#8a6a45 100%)"></div><h3>Brightmoor Article&nbsp; 3</h3><div class="meta"><span class="tag">Physically</span><span class="date">/ Jan 2020</span></div><p>Welcome to Brightmoor.&nbsp;&nbsp; An investigation of how spending time in nature helps you to feel better - physically, mentally, spiritually.</p></article>
    <article class="post"><div class="thumb" role="img" aria-label="Woman in a hat in golden sunset light" style="background:linear-gradient(160deg,#2e2a1c,#d8a050 45%,#5a3324 80%)"></div><h3>Brightmoor Article&nbsp; 4</h3><div class="meta"><span class="tag">mentally</span><span class="date">/ Jan 2020</span></div><p>Welcome to Brightmoor.&nbsp;&nbsp; An investigation of how spending time in nature helps you to feel better - physically, mentally, spiritually.</p></article>
    <article class="post"><div class="thumb" role="img" aria-label="Close-up of a palm leaf" style="background:linear-gradient(135deg,#1f2f14,#8a9a44 50%,#2d3f1c)"></div><h3>Brightmoor Article&nbsp; 5</h3><div class="meta"><span class="tag">spiritually</span><span class="date">/ Jan 2020</span></div><p>Welcome to Brightmoor.&nbsp;&nbsp; An investigation of how spending time in nature helps you to feel better - physically, mentally, spiritually.</p></article>
    <article class="post"><div class="thumb" role="img" aria-label="Woman in white in a green meadow" style="background:linear-gradient(180deg,#3f5a2c,#9aa386 50%,#6e8a4a)"></div><h3>Brightmoor Article&nbsp; 6</h3><div class="meta"><span class="tag">Physically</span><span class="date">/ Jan 2020</span></div><p>Welcome to Brightmoor.&nbsp;&nbsp; An investigation of how spending time in nature helps you to feel better - physically, mentally, spiritually.</p></article>
    <article class="post"><div class="thumb" role="img" aria-label="Woman in a cap on a dusty hillside" style="background:linear-gradient(180deg,#6a7a5a,#b08560 40%,#8e7a68 100%)"></div><h3>Brightmoor Article 7</h3><div class="meta"><span class="tag">mentally</span><span class="date">/ Jan 2020</span></div><p>Welcome to Brightmoor.&nbsp;&nbsp; An investigation of how spending time in nature helps you to feel better - physically, mentally, spiritually.</p></article>
    <article class="post"><div class="thumb" role="img" aria-label="Dry dunes under a grey sky" style="background:linear-gradient(180deg,#4c5156 0%,#80807a 45%,#b49a68 65%,#7a6444 100%)"></div><h3>Brightmoor Article&nbsp; 8</h3><div class="meta"><span class="tag">Physically</span><span class="date">/ Jan 2020</span></div><p>Welcome to Brightmoor.&nbsp;&nbsp; An investigation of how spending time in nature helps you to feel better - physically, mentally, spiritually.</p></article>
    <article class="post"><div class="thumb" role="img" aria-label="Butterfly resting on pebbles" style="background:linear-gradient(135deg,#9a8468,#5e4e3c 50%,#a8937a)"></div><h3>Brightmoor Article&nbsp; 9</h3><div class="meta"><span class="tag">spiritually</span><span class="date">/ Jan 2020</span></div><p>Welcome to Brightmoor.&nbsp;&nbsp; An investigation of how spending time in nature helps you to feel better - physically, mentally, spiritually.</p></article>
  </div>
  <div class="abs pager" style="left:207px"></div>
  <div class="abs pager" style="left:255px"></div>
  <div class="abs view-all">View All<span>&gt;</span></div>
</section>

<section>
  <div class="abs sub-frame"></div>
  <div class="abs sub-light">Subscribe</div>
  <div class="abs sub-dark">
    <div class="label">Email Address</div>
    <div class="field"></div>
    <div class="send"><svg width="16" height="14" viewBox="0 0 16 14" aria-label="Send"><path d="M1 1l14 6-14 6 3-6z M4 7h11" fill="none" stroke="#1d1f21" stroke-width="1.3" stroke-linejoin="round"/></svg></div>
  </div>
</section>

<footer class="abs site-footer">
  <ul>
    <li>Joan Petrie</li>
    <li>Brightmoor</li>
    <li>Telephone +44 7700 900417</li>
    <li>brightmoor@mailvane.com</li>
  </ul>
</footer>
<div class="abs copyright">Copyright 2020 Brightmoor</div>

</body>
</html>
```